Web Design Services Create a Similar website to my Competitor

We would like a similar website designed like our main competitor with all the features there website has and more. Also we would like to accept payments through our website and to rank quickly with seo based on our home page and other page use of high traffic keywords. this is the website we would like to have ours designed similar to https://www.harbourpetalstudio.com. we will be providing the same services and more just at a different location. We would also like to know be able to easily make adjustments to the website when its time to edit it please thanks.

Basically I am looking to have have similar website built almost exactly the same but with my logo, and other personalized information to my company Rosalind Marigold Beauty Lounge. I will need to send you model images and logo design idea but the body and user interface of my competitor https://www.harbourpetalstudio.com will be exactly the same. I can be reached anytime to answer any questions you may have.
Updates

Hi Designers I would like to clarify some information Harbour Petal Studio is my Competitor we are not affiliated. I would like my website to be designed similar to hers but please do not take any content from her website to put on mine I will be providing images to be posted on my website. Also please do not use any of her videos or YouTube videos on my website to avoid any legal issues. Thanks for your understanding.

Target Market(s)

Make up Application Services For Events and Lindenbrook Summer Festival

Industry/Entity Type

Beauty and Makeup Application and services

Coding

Coded - Design and coding required

Number of Pages Required

5+ page

Font styles to use
Sans Serif

Colors
E54698
E96AAD
F1A4CE
F9D9EA
FCEFF6
A7469A
B969AE
D3A5CF
EDDBEB
F8F0F9

Requirements
Must have
• Must be similar to my competitor, need a video section, testimonial and must be easily able to navigate to information sections and book now payment notifications running on all pages so customers can easily book there spot for 2026 carnival
Nice to have
• I am looking to have a similar website to https://www.harbourpetalstudio.com created but make it as minimal and modern
Should not have
• Project can be coded if it makes it easier to create a similar look to my competitor just ask that updates can easily be made later on.

```html
<!DOCTYPE html>
<html lang="en">
<head>
<meta charset="utf-8">
<title>Rosalind Marigold Beauty Lounge</title>
<link href="https://fonts.googleapis.com/css2?family=Montserrat:wght@400;500;600;700&display=swap" rel="stylesheet">
<style>
:root{
  --pink:#E54698;
  --pink-mid:#E96AAD;
  --pink-soft:#F1A4CE;
  --blush:#F9D9EA;
  --mist:#F6EEF5;
  --ink:#1c1c1c;
  --text:#333;
  --white:#fff;
  --footer:#0d0d0d;
}
*{box-sizing:border-box;margin:0;padding:0}
html,body{width:1200px;height:3670px;overflow:hidden}
body{font-family:'Montserrat',sans-serif;color:var(--text);background:var(--white);position:relative}
.abs{position:absolute}
.photo{position:absolute;overflow:hidden}

/* Header */
.site-header{left:137px;top:0;width:925px;height:94px;background:var(--white);border-radius:0 0 16px 16px;z-index:5}
.brand{left:28px;top:18px;color:var(--pink);font-weight:700;font-size:20px;line-height:1.1;width:230px}
.brand small{display:block;font-size:13px;font-weight:600;padding-left:60px}
.main-nav{left:338px;top:43px;display:flex;gap:34px;font-size:14px;color:#333;white-space:nowrap}
.main-nav .active{color:var(--pink);font-weight:600}
.search-btn{left:874px;top:38px;width:32px;height:32px;border-radius:50%;background:var(--pink)}

/* Hero */
.hero{left:0;top:0;width:1200px;height:717px;background:radial-gradient(ellipse at 72% 40%,#c98a6a 0%,#6a3f52 25%,#1f4a6c 55%,#0e2436 100%)}
.hero-curve{left:0;top:560px}
.hero-title{left:118px;top:232px;width:400px;color:var(--white);font-weight:700;font-size:38px;line-height:1.1;white-space:nowrap;text-align:right}
.hero-title span{display:block;font-size:26px;font-weight:600;text-align:right;padding-right:10px;margin-top:4px}
.hero-text{left:140px;top:354px;width:350px;text-align:right;color:var(--white);font-size:18px;line-height:24px}
.btn{position:absolute;background:var(--pink);color:var(--white);font-weight:700;font-size:15px;border-radius:22px;display:flex;align-items:center;justify-content:center;white-space:nowrap}
.hero-dots{left:1017px;top:310px}
.hero-dots i{display:block;width:6px;height:6px;border-radius:50%;background:var(--pink);margin-bottom:20px}
.hero-dots i.on{background:var(--white)}

.section-title{position:absolute;left:0;width:1200px;text-align:center;color:var(--pink);font-weight:700;font-size:36px}

/* Destinations */
.dest-card{top:829px;width:288px;height:372px;border-radius:14px}
.dest-card .shade{position:absolute;left:0;right:0;bottom:0;height:190px;background:linear-gradient(to bottom,rgba(229,70,152,0),rgba(229,70,152,.95))}
.dest-date{position:absolute;left:21px;bottom:54px;color:var(--white);font-size:12px}
.dest-name{position:absolute;left:21px;bottom:24px;color:var(--white);font-weight:700;font-size:25px}
.dest-badge{position:absolute;right:19px;bottom:24px;width:42px;height:42px;border-radius:50%;background:#1e1e1e;border:2px solid rgba(255,255,255,.5)}
.slider-arrows{left:574px;top:1252px}

/* Without us */
.without-title{left:141px;top:1314px;width:520px;color:var(--pink);font-weight:700;font-size:39px;line-height:43px}
.without-list{left:688px;top:1318px;list-style:none;font-size:15px;line-height:30.5px;color:#333;white-space:nowrap}

/* About band */
.about-band{left:0;top:1553px;width:1200px;height:495px;background:var(--mist)}
.about-media{left:138px;top:1613px;width:540px;height:346px;border-radius:16px;background:linear-gradient(135deg,#3a1a10 0%,#b5561e 40%,#7a3a22 65%,#1e0f0c 100%)}
.play-small{left:649px;top:1751px;width:50px;height:50px;border-radius:50%;background:var(--pink)}
.about-copy{left:721px;top:1610px;width:340px;display:flex;flex-direction:column}
.about-title{color:var(--pink);font-weight:700;font-size:33px;line-height:37px}
.about-quote{margin-top:20px;width:320px;font-size:14px;line-height:19.5px;color:#333}
.about-name{margin-top:18px;font-weight:700;font-size:14px;color:#222}

/* Testimonial video */
.review-video{left:138px;top:2147px;width:925px;height:478px;border-radius:16px;background:linear-gradient(110deg,#0f0e12 0%,#2a2326 35%,#5a6f9a 60%,#8fb3da 80%,#2b3a5a 100%)}
.play-large{left:557px;top:2315px;width:86px;height:86px;border-radius:50%;background:rgba(60,60,60,.6)}

/* Gallery */
.gallery-band{left:0;top:2683px;width:1200px;height:613px;background:var(--mist)}
.gallery-item{width:221px;height:222px;border-radius:12px}

/* Newsletter */
.newsletter{left:0;top:3296px;width:1200px;height:110px;background:var(--pink)}
.newsletter h2{position:absolute;left:147px;top:30px;color:var(--white);font-weight:700;font-size:34px;white-space:nowrap}
.news-field{left:567px;top:31px;width:476px;height:47px;background:var(--white);border-radius:24px;font-size:15px;color:#333;padding:14px 0 0 26px}
.news-submit{left:352px;top:0;width:124px;height:47px;background:#111;color:var(--white);border-radius:24px;font-size:15px;display:flex;align-items:center;justify-content:center}

/* Footer */
.site-footer{left:0;top:3406px;width:1200px;height:225px;background:var(--footer);color:var(--white)}
.foot-brand{left:133px;top:30px;color:var(--pink);font-weight:700;font-size:24px;line-height:1.1;width:260px;white-space:nowrap}
.foot-brand small{display:block;font-size:15px;padding-left:90px;color:var(--pink)}
.socials{left:263px;top:112px;display:flex;gap:17px}
.socials i{display:block;width:20px;height:20px;border-radius:50%;background:var(--pink)}
.foot-col h4{font-size:16px;font-weight:700;margin-bottom:12px}
.foot-col ul{list-style:none;font-size:15px;line-height:24px}
.foot-col li{display:flex;align-items:center;gap:12px;white-space:nowrap}
.contact-col li{align-items:flex-start;gap:9px}
.contact-col svg{margin-top:5px;flex:none}
.copyright{left:0;top:3631px;width:1200px;height:39px;background:var(--pink);color:var(--white);font-size:12px;text-align:center;padding-top:13px}
</style>
</head>
<body>

<section class="hero abs" role="img" aria-label="Close-up portrait of a woman in glittering carnival makeup and jewelled headdress"></section>
<svg class="hero-curve abs" width="1200" height="158" viewBox="0 0 1200 158"><path d="M0 158 Q600 -14 1200 158 Z" fill="#fff"/></svg>

<header class="site-header abs">
  <div class="brand abs">Rosalind Marigold<small>Beauty Lounge</small></div>
  <nav class="main-nav abs">
    <span class="active">Home</span><span>Rosalind Marigold Anywhere</span><span>Store</span><span>More</span><span>Contact</span>
  </nav>
  <div class="search-btn abs">
    <svg width="32" height="32" viewBox="0 0 32 32"><circle cx="15" cy="15" r="4.5" fill="none" stroke="#fff" stroke-width="2"/><line x1="18.3" y1="18.3" x2="21.5" y2="21.5" stroke="#fff" stroke-width="2" stroke-linecap="round"/></svg>
  </div>
</header>

<h1 class="hero-title abs">Rosalind Marigold<span>Beauty Lounge</span></h1>
<p class="hero-text abs">Lorem ipsum dolor sit amet, consectetur adipiscing elit, commodo viverra maecenas accumsan</p>
<a class="btn" style="left:356px;top:446px;width:133px;height:41px">Book Now</a>
<div class="hero-dots abs"><i></i><i class="on"></i><i></i><i></i></div>

<h2 class="section-title" style="top:738px">Choose Your Destination</h2>

<article class="dest-card photo" style="left:138px;background:linear-gradient(160deg,#e8902e,#8a3a4a 45%,#3b2340)" role="img" aria-label="Smiling reveller in a rainbow feathered headdress">
  <div class="shade"></div><span class="dest-date">26 Oct 2025</span><span class="dest-name">Tobago</span><span class="dest-badge"></span>
</article>
<article class="dest-card photo" style="left:456px;background:linear-gradient(170deg,#2a1418,#7a1e2a 40%,#c8334a 70%)" role="img" aria-label="Dancer in a red feathered carnival costume">
  <div class="shade"></div>
  <a class="btn" style="left:56px;top:161px;width:161px;height:42px;font-size:14px">Choose Now</a>
  <span class="dest-date">26 Oct 2025</span><span class="dest-name">Miami</span><span class="dest-badge"></span>
</article>
<article class="dest-card photo" style="left:772px;background:linear-gradient(150deg,#3fa6d6,#e9862e 45%,#d6486e 80%)" role="img" aria-label="Reveller in orange feathers and sunglasses among confetti">
  <div class="shade"></div><span class="dest-date" style="bottom:50px">26 Oct 2025</span><span class="dest-name" style="bottom:20px">Toronto</span><span class="dest-badge"></span>
</article>

<svg class="slider-arrows abs" width="50" height="20" viewBox="0 0 50 20"><path d="M11 3 L4 10 L11 17" fill="none" stroke="#111" stroke-width="2.2"/><path d="M38 3 L45 10 L38 17" fill="none" stroke="#111" stroke-width="2.2"/></svg>

<h2 class="without-title abs">Without Us, Your<br>Carnival Morning Might<br>Look Like This:</h2>
<a class="btn" style="left:140px;top:1462px;width:161px;height:41px">See Packages</a>
<ul class="without-list abs">
  <li>Lorem ipsum dolor sit amet,</li>
  <li>Consectetur adipiscing elit, sed do eiusmod tempor</li>
  <li>Incididunt ut labore et dolore magna aliqua.</li>
  <li>Quis ipsum suspendisse ultrices gravida.</li>
  <li>Risus commodo viverra maecenas accumsan</li>
</ul>

<section class="about-band abs"></section>
<div class="about-media photo" role="img" aria-label="Video still of a smiling woman wearing carnival face paint and orange feathers"></div>
<div class="play-small abs"><svg width="50" height="50" viewBox="0 0 50 50"><path d="M21 17 L32 25 L21 33 Z" fill="#fff"/></svg></div>
<div class="about-copy abs">
  <h2 class="about-title">More Than Just Makeup, Rosalind Marigold Beauty Is An Experience</h2>
  <p class="about-quote">“Lorem ipsum dolor sit amet, consectetur adipiscing elit, sed do eiusmod tempor incididunt ut labore et dolore magna aliqua. Quis ipsum suspendisse ultrices gravida. Risus commodo viverra maecenas accumsan lacus vel facilisis”</p>
  <p class="about-name">- Talia</p>
</div>

<h2 class="section-title" style="top:2075px">What People Says About Us</h2>
<div class="review-video photo" role="img" aria-label="Video still of an artist painting a blue and red design on a client's face"></div>
<div class="play-large abs"><svg width="86" height="86" viewBox="0 0 86 86"><path d="M37 30 L55 43 L37 56 Z" fill="#fff"/></svg></div>

<section class="gallery-band abs"></section>
<h2 class="section-title" style="top:2708px">Gallery</h2>
<div class="gallery-item photo" style="left:137px;top:2794px;background:linear-gradient(135deg,#3e9a6a,#d6a23a 50%,#8a3a2a)" role="img" aria-label="Gallery: green and gold carnival makeup"></div>
<div class="gallery-item photo" style="left:371px;top:2794px;background:linear-gradient(135deg,#c9852a,#7a4422 55%,#b5891e)" role="img" aria-label="Gallery: jewelled face makeup with golden feathers"></div>
<div class="gallery-item photo" style="left:605px;top:2794px;background:linear-gradient(135deg,#1d2a26,#2f6a58 45%,#9a6a2a)" role="img" aria-label="Gallery: laughing reveller in a teal headdress"></div>
<div class="gallery-item photo" style="left:839px;top:2794px;background:linear-gradient(135deg,#e5a8d6,#c97ac6 45%,#f2d5e6)" role="img" aria-label="Gallery: pastel feathered mask"></div>
<div class="gallery-item photo" style="left:137px;top:3031px;background:linear-gradient(135deg,#b5301e,#6a2a1a 50%,#2ab0b8)" role="img" aria-label="Gallery: red and gold glitter makeup"></div>
<div class="gallery-item photo" style="left:371px;top:3031px;background:linear-gradient(135deg,#6a4a2a,#3e8ab8 50%,#c9a45a)" role="img" aria-label="Gallery: blue gem eye makeup"></div>
<div class="gallery-item photo" style="left:605px;top:3031px;background:linear-gradient(135deg,#3a2418,#a86a3a 50%,#d6a24a)" role="img" aria-label="Gallery: gold glitter freckle makeup"></div>
<div class="gallery-item photo" style="left:839px;top:3031px;background:linear-gradient(135deg,#d6922a,#8a4a2a 50%,#2a6a8a)" role="img" aria-label="Gallery: jewelled headpiece and sequinned costume"></div>
<svg class="abs" style="left:56px;top:3004px" width="16" height="20" viewBox="0 0 16 20"><path d="M11 3 L4 10 L11 17" fill="none" stroke="#111" stroke-width="2.2"/></svg>
<svg class="abs" style="left:1122px;top:3006px" width="16" height="20" viewBox="0 0 16 20"><path d="M5 3 L12 10 L5 17" fill="none" stroke="#111" stroke-width="2.2"/></svg>

<section class="newsletter abs">
  <h2>Newsletter Subscribe</h2>
  <div class="news-field abs">Enter email id<span class="news-submit abs">Subscribe</span></div>
</section>

<footer class="site-footer abs">
  <div class="foot-brand abs">Rosalind Marigold<small>Beauty Lounge</small></div>
  <div class="socials abs" role="img" aria-label="Social media links"><i></i><i></i><i></i></div>
  <div class="foot-col abs" style="left:520px;top:46px">
    <h4>Quick Links</h4>
    <ul>
      <li><svg width="7" height="11" viewBox="0 0 7 11"><path d="M1 1 L5.5 5.5 L1 10" fill="none" stroke="#E54698" stroke-width="1.8"/></svg>Home</li>
      <li><svg width="7" height="11" viewBox="0 0 7 11"><path d="M1 1 L5.5 5.5 L1 10" fill="none" stroke="#E54698" stroke-width="1.8"/></svg>Rosalind Marigold Anywhere</li>
      <li><svg width="7" height="11" viewBox="0 0 7 11"><path d="M1 1 L5.5 5.5 L1 10" fill="none" stroke="#E54698" stroke-width="1.8"/></svg>Store</li>
      <li><svg width="7" height="11" viewBox="0 0 7 11"><path d="M1 1 L5.5 5.5 L1 10" fill="none" stroke="#E54698" stroke-width="1.8"/></svg>More</li>
      <li><svg width="7" height="11" viewBox="0 0 7 11"><path d="M1 1 L5.5 5.5 L1 10" fill="none" stroke="#E54698" stroke-width="1.8"/></svg>Contact</li>
    </ul>
  </div>
  <div class="foot-col contact-col abs" style="left:856px;top:42px">
    <h4>Contact</h4>
    <ul>
      <li><svg width="13" height="15" viewBox="0 0 13 15"><path d="M6.5 0.5 C3.3 0.5 1 2.8 1 5.8 C1 9.5 6.5 14.5 6.5 14.5 C6.5 14.5 12 9.5 12 5.8 C12 2.8 9.7 0.5 6.5 0.5 Z" fill="#E54698"/><circle cx="6.5" cy="5.8" r="2" fill="#0d0d0d"/></svg><span>#123, Lorium ipsum<br>dolor amit,<br>city.NJ</span></li>
      <li><svg width="13" height="14" viewBox="0 0 13 14"><path d="M2.5 1 L5 1 L6 4 L4.5 5.3 C5.3 7.2 6.6 8.5 8.5 9.4 L9.8 8 L12.5 9 L12.5 11.5 C12.5 12.5 11.7 13 10.8 13 C5.5 12.5 1.3 8.3 1 3 C1 1.8 1.6 1 2.5 1 Z" fill="#E54698"/></svg><span>1800 555 0142</span></li>
      <li><svg width="13" height="14" viewBox="0 0 13 14"><rect x="0.5" y="3" width="12" height="9" rx="1" fill="#E54698"/><path d="M0.8 3.5 L6.5 8 L12.2 3.5" fill="none" stroke="#0d0d0d" stroke-width="1.2"/></svg><span>info@rosalindmarigold.com</span></li>
    </ul>
  </div>
</footer>
<div class="copyright abs">© 2025 &nbsp;|&nbsp; www.rosalindmarigoldbeautylounge.com</div>

</body>
</html>
```